Web Developer Needs a Business Card Design

I need a personal business card design that represents me as a web developer for potential employers. I would like the background to be a dark color on the front for contrast with my logo and name. The back will have all my information along with a smaller version of the logo. I want something with a modern look and feel, not too conservative. This will be used for potential employers and freelance work.

Industry/Entity Type

Business

Contact Information for Business Card

Front should have my logo and name. The back should have all my personal information which would include: name: Tom Varulek, phone: 570-614-3098, email: tomvarulek@quillbox.net, website url: www.tomvarulek.net, logo, web developer.

Font styles to use
Sans Serif

Requirements
Must have
• Must include my logo. The color palette base color will be the logo color.

```html
<!DOCTYPE html>
<html lang="en">
<head>
<meta charset="utf-8">
<title>Tom Varulek — Business Card</title>
<link rel="stylesheet" href="https://fonts.googleapis.com/css2?family=Roboto:wght@400;500;700&display=swap">
<style>
  :root {
    --backdrop: #2b2624;
    --card: #121212;
    --card-edge: #1c1c1c;
    --teal: #5ec9b1;
    --silver: #c9c9c9;
    --silver-dim: #6a6a6a;
    --ink: #ffffff;
    --icon-glyph: #121212;
  }
  * { margin: 0; padding: 0; box-sizing: border-box; }
  html, body {
    width: 1200px;
    height: 780px;
    overflow: hidden;
    background: var(--backdrop);
    font-family: "Roboto", Arial, sans-serif;
  }
  .sheet {
    width: 1200px;
    height: 780px;
    display: flex;
    align-items: center;
    justify-content: center;
    gap: 40px;
  }
  .card {
    position: relative;
    width: 540px;
    height: 309px;
    background: var(--card);
    border: 1px solid var(--card-edge);
    border-radius: 4px;
    box-shadow: 0 14px 30px rgba(0, 0, 0, 0.45);
    overflow: hidden;
  }

  /* Front */
  .front-ring {
    position: absolute;
    left: 50%;
    top: 48px;
    width: 150px;
    height: 150px;
    margin-left: -75px;
    border: 7px solid var(--silver);
    border-radius: 50%;
  }
  .front-name {
    position: absolute;
    left: 0;
    right: 0;
    top: 218px;
    text-align: center;
    font-size: 26px;
    font-weight: 700;
    color: var(--silver-dim);
    letter-spacing: 0.5px;
  }

  /* Back */
  .back-ring {
    position: absolute;
    left: 276px;
    top: 28px;
    width: 112px;
    height: 112px;
    border: 6px solid var(--teal);
    border-radius: 50%;
  }
  .identity {
    position: absolute;
    right: 292px;
    top: 150px;
    text-align: right;
    color: var(--ink);
  }
  .identity-name {
    font-size: 25px;
    font-weight: 700;
    line-height: 1.1;
  }
  .identity-role {
    font-size: 19px;
    font-weight: 500;
    line-height: 1.2;
  }
  .divider {
    position: absolute;
    left: 272px;
    top: 174px;
    width: 2px;
    height: 96px;
    background: var(--ink);
  }
  .contact-list {
    position: absolute;
    left: 292px;
    top: 180px;
    list-style: none;
  }
  .contact-item {
    display: flex;
    align-items: center;
    gap: 18px;
    height: 28px;
    color: var(--ink);
    font-size: 16px;
  }
  .contact-icon {
    width: 15px;
    height: 15px;
    flex: none;
  }
</style>
</head>
<body>
  <main class="sheet">
    <section class="card card-front" aria-label="Card front">
      <div class="front-ring"></div>
      <p class="front-name">Tom Varulek</p>
    </section>

    <section class="card card-back" aria-label="Card back">
      <div class="back-ring"></div>
      <div class="identity">
        <p class="identity-name">Tom Varulek</p>
        <p class="identity-role">Web Developer</p>
      </div>
      <div class="divider"></div>
      <ul class="contact-list">
        <li class="contact-item">
          <svg class="contact-icon" viewBox="0 0 16 16" aria-hidden="true">
            <rect width="16" height="16" rx="3" fill="var(--ink)"/>
            <path d="M4.5 3.5h2l1 2.5-1.3 1a6 6 0 0 0 2.8 2.8l1-1.3 2.5 1v2a1 1 0 0 1-1 1A8.5 8.5 0 0 1 3.5 4.5a1 1 0 0 1 1-1z" fill="var(--icon-glyph)"/>
          </svg>
          <span>570-614-3098</span>
        </li>
        <li class="contact-item">
          <svg class="contact-icon" viewBox="0 0 16 16" aria-hidden="true">
            <rect width="16" height="16" rx="3" fill="var(--ink)"/>
            <rect x="3" y="4.5" width="10" height="7" fill="var(--icon-glyph)"/>
            <path d="M3 4.5l5 4 5-4" fill="none" stroke="var(--ink)" stroke-width="1"/>
          </svg>
          <span>tomvarulek@quillbox.net</span>
        </li>
        <li class="contact-item">
          <svg class="contact-icon" viewBox="0 0 16 16" aria-hidden="true">
            <rect width="16" height="16" rx="3" fill="var(--ink)"/>
            <circle cx="8" cy="8" r="4.6" fill="none" stroke="var(--icon-glyph)" stroke-width="1.3"/>
            <ellipse cx="8" cy="8" rx="2" ry="4.6" fill="none" stroke="var(--icon-glyph)" stroke-width="1"/>
            <path d="M3.4 8h9.2" stroke="var(--icon-glyph)" stroke-width="1"/>
          </svg>
          <span>www.tomvarulek.net</span>
        </li>
      </ul>
    </section>
  </main>
</body>
</html>
```